Private Investigation Business Card Design

I need a business card for a new private investigation company named Brisk Inquiries. I perform mainly surveillance jobs, vehicle repossessions, document serves etc. The final design should aim for a professional look. The logo has a magnifying glass with stick man arms and legs and is in a running action to show the "Brisk" aspect of the name. If the colour scheme could remain the same as the website www.briskinquiries-demo.com.au with silvers,blacks and a couple electric blue highlights.
Industry/Entity Type
Business
Contact Information for Business Card
Morgan Kellaway
Brisk Inquiries
0487316204
PO Box 58, Carnwell NSW 2291
info@briskinquiries-demo.com.au
www.briskinquiries-demo.com.au
Look and feel

```html
<!DOCTYPE html>
<html lang="en">
<head>
<meta charset="utf-8">
<title>Brisk Inquiries – Business Card</title>
<link href="https://fonts.googleapis.com/css2?family=Saira:wght@400;600&family=Open+Sans:ital,wght@1,400&display=swap" rel="stylesheet">
<style>
  :root {
    --backdrop: #3b3b3b;
    --card-white: #f7f7f7;
    --ink: #2a2a2a;
    --ink-soft: #4a4a4a;
    --rule: #c9c9c9;
    --band-dark: #1d1b1c;
    --band-silver-a: #8c8a8c;
    --band-silver-b: #d8d6d8;
    --back-light: #d2d2d2;
    --back-dark: #8e8e8e;
    --brand-silver: #6f6f6f;
  }
  * { margin: 0; padding: 0; box-sizing: border-box; }
  html, body { width: 1200px; height: 750px; overflow: hidden; }
  body { background: var(--backdrop); position: relative; font-family: "Saira", sans-serif; color: var(--ink); }

  .card { position: absolute; left: 371px; width: 461px; height: 263px; box-shadow: 0 3px 8px rgba(0,0,0,.45); overflow: hidden; }
  .card-front { top: 101px; background: var(--card-white); }
  .card-back { top: 401px; background: radial-gradient(ellipse at 50% 45%, var(--back-light) 0%, #b4b4b4 55%, var(--back-dark) 100%); }

  .brand { position: absolute; display: flex; align-items: center; gap: 8px; }
  .brand-name { font-weight: 600; color: var(--brand-silver); line-height: 1; letter-spacing: 1px; }
  .brand-dot { border-radius: 50%; border: 2px solid var(--brand-silver); }

  .card-front .brand { right: 32px; top: 32px; }
  .card-front .brand-name { font-size: 28px; }
  .card-front .brand-dot { width: 22px; height: 22px; }

  .holder-name { position: absolute; left: 30px; top: 138px; font-size: 16px; font-weight: 600; color: var(--ink); }
  .divider { position: absolute; left: 30px; top: 166px; width: 393px; height: 1px; background: var(--rule); }

  .contact-list { position: absolute; left: 30px; top: 178px; list-style: none; }
  .contact-list li { display: flex; align-items: center; gap: 6px; font-size: 10.5px; color: var(--ink-soft); height: 17.5px; }
  .contact-list li.phone { font-size: 12px; }
  .contact-list svg { width: 11px; height: 11px; fill: var(--ink); flex: none; }

  .postal { position: absolute; right: 32px; top: 200px; text-align: right; font-size: 10.5px; line-height: 14.5px; color: var(--ink-soft); font-style: normal; }

  .band { position: absolute; left: 0; bottom: 0; width: 100%; height: 11px; }

  .card-back .brand { left: 50%; top: 100px; transform: translateX(-50%); flex-direction: column; gap: 10px; }
  .card-back .brand-name { font-size: 30px; color: var(--ink); }
  .card-back .brand-dot { width: 40px; height: 40px; border-color: var(--ink); order: -1; }

  .back-url { position: absolute; left: 0; width: 100%; top: 210px; text-align: center; font-family: "Open Sans", sans-serif; font-style: italic; font-size: 10.5px; letter-spacing: 3.2px; color: var(--ink-soft); }
</style>
</head>
<body>

<section class="card card-front">
  <div class="brand">
    <span class="brand-name">Brisk</span>
    <span class="brand-dot"></span>
  </div>

  <h1 class="holder-name">Morgan Kellaway</h1>
  <div class="divider"></div>

  <ul class="contact-list">
    <li class="phone">
      <svg viewBox="0 0 24 24"><path d="M6.6 10.8a15.1 15.1 0 0 0 6.6 6.6l2.2-2.2a1 1 0 0 1 1-.25 11.4 11.4 0 0 0 3.6.57 1 1 0 0 1 1 1V20a1 1 0 0 1-1 1A17 17 0 0 1 3 4a1 1 0 0 1 1-1h3.5a1 1 0 0 1 1 1c0 1.25.2 2.45.57 3.6a1 1 0 0 1-.25 1z"/></svg>
      0487 316 204
    </li>
    <li>
      <svg viewBox="0 0 24 24"><path d="M2 5h20v14H2z M3.5 6.5v.6L12 12.6l8.5-5.5v-.6z" fill-rule="evenodd"/></svg>
      info@briskinquiries-demo.com.au
    </li>
    <li>
      <svg viewBox="0 0 24 24"><circle cx="12" cy="12" r="10"/><path d="M7 8c2 0 3 1 3 3s-2 1-2 3 2 2 2 4M15 5c-1 2 1 3 2 3s3 1 2 4" stroke="#f7f7f7" stroke-width="1.6" fill="none"/></svg>
      www.briskinquiries-demo.com.au
    </li>
  </ul>

  <address class="postal">PO Box 58<br>Carnwell NSW 2291</address>

  <svg class="band" viewBox="0 0 461 11" preserveAspectRatio="none">
    <defs>
      <linearGradient id="bandSilver" x1="0" x2="1" y1="0" y2="0">
        <stop offset="0" stop-color="var(--band-silver-a)"/>
        <stop offset="1" stop-color="var(--band-silver-b)"/>
      </linearGradient>
    </defs>
    <polygon points="0,0 302,0 299,11 0,11" fill="url(#bandSilver)"/>
    <polygon points="306,0 461,0 461,11 302,11" fill="var(--band-dark)"/>
  </svg>
</section>

<section class="card card-back">
  <div class="brand">
    <span class="brand-dot"></span>
    <span class="brand-name">Brisk Inquiries</span>
  </div>
  <p class="back-url">www.briskinquiries-demo.com.au</p>
</section>

</body>
</html>
```